Simple informational site
Target viewers are prime &subcontractors (construction)
Rook42: Thank you for all of your drafts! You really put some thought into the latest ones. We liked your most recent submissions. It was a tough choice. We look forward to seeing more of your work in the future.
comments please...............
tolvane: Thank you for your drafts. They are being considered.
All
As far as posted times on the draft sites:
1. if TWO times are posted, please label respectively - "Guam" & "Hawaii"
2. if THREE times are posted, please label respectively - "Guam", "Hawaii" and "East Coast"
VelvetTurnip: we prefer the gray and blue drafts. Also, thank you for including the news feed via RSS.
Rook42: We like the dual-tone shaded site. Thanks.
All - Regarding the "Contact Us" page: we would prefer the page have e-mail capability via a form that has spam prevention capability (e.g. having to enter a random image of letters/numbers).
Rook42: Thank you for your reshaded drafts. We like the dual tone.
All - Thank you for your submissions. Due to the time difference (it is currently 6:45 a.m. where we are located), we were unable to provide immediate feedback. We have approximately 5 hours remaining in our contest. We will begin the draft elimination process shortly; finalization to follow before end of contest.
Hi PH, new draft is with light color as per instrcution, waiting for your valuable feedback
Thanks!
I submitted 2 new drafts with some variation in color, new background and a news section. If they're too dark or if there is anything you don't like let me know. I might work on some different colored versions later on today as well.
VelvetTurnp: we find your website the most responsive to our brief and other comments. We would prefer a different background and a bit bolder color scheme. Thank you.
Rook42: Your site is appealing to most members of our team. Some commented that they like the shades of blue background, while others would prefer lighter colors. We feel that the logo looks like it was stuck on the site like a sticker - a bit out of place. Your news feed is very well received.
maribel: Thank you for your draft. We appreciate the clean design. We have no further comments at this time.
Kelunramesh: Your draft sites are clean and simple. We do not have further comments at this time. Thank you.
Hi PH, your feedback is welcomed, waiting for your valuable comments if you need any change or variation :)
I'm glad you like it. Let me know if there's any changes you would like to see.
VelvetTurnip - we like that your site has a lot of info, but easy to read and navigate. We like that the section headings "grab" our attention well.
Rook42 - thanks for the different versions. We like the details you included: news feed, date and time. The drafts are clean.
reference website in October 11, 2010 4:57 p.m. comment in this discussion string. www.tarnbuildersexample.com
Whats the refrence website?
Designers - the Company logo has been finalized. Refer to http://orders.markcraftexample.com/contests/pelora-keystone
Regarding questions as to website, we've provided a reference website; the tabs on the referenced site contains almost all that we're looking for.
The site will NOT need links for purchasing.
Home page: should accommodate a brief introduction of the Company and have other pages clearly listed.
Products page: should be able to have products listed. Target customers are prime contractors; technical product data is important. Products include but are not limited to concrete, cement, aggregates, asphalt and tile.
Small business page: should be able to accommodate information as to Company's small business certification which assist federal contractors achieve small business goals
Contact page: should have email inquiry link, Company address and contact numbers
Many prospective contractors do not know much about the island of Guam. We're considering adding a page containing information about Guam.
I hope this helps!
Hi PH,
Submit will design soon.
Regards
I will submit my design soon.

```html
<!DOCTYPE html>
<html lang="en">
<head>
<meta charset="utf-8">
<title>PELORA Keystone</title>
<link href="https://fonts.googleapis.com/css2?family=Arimo:wght@400;700&display=swap" rel="stylesheet">
<style>
:root{
  --page:#ffffff;
  --sky-top:#dfeaf3;
  --sky-bottom:#b9cfe0;
  --hero-text:#8fa6b8;
  --blue:#2f6fb2;
  --blue-dark:#1d4f86;
  --side:#4d6475;
  --side-dark:#3c5060;
  --panel:#8fa4b3;
  --panel-light:#a9bac6;
  --ink:#1d2a33;
  --text-light:#eef3f7;
  --footer:#3d4a55;
  --news-box:#6f8797;
}
*{margin:0;padding:0;box-sizing:border-box}
html,body{width:1200px;height:1070px;overflow:hidden;background:var(--page)}
body{font-family:"Arimo",Arial,sans-serif;color:var(--ink);position:relative}
.header{position:absolute;left:0;top:0;width:1200px;height:95px;background:var(--page)}
.brand{position:absolute;left:140px;top:18px;display:flex;align-items:center;gap:12px}
.brand-mark{width:46px;height:46px;background:var(--side)}
.brand-name{font-size:30px;font-weight:700;color:var(--ink);line-height:1}
.newsfeed{position:absolute;left:470px;top:10px;font-size:13px;color:var(--blue)}
.newsfeed b{color:var(--blue-dark)}
.datebox{position:absolute;right:85px;top:10px;text-align:right;font-size:13px;color:var(--blue-dark)}
.datebox .times{margin-top:14px;font-weight:700}
.hero{position:absolute;left:0;top:95px;width:1200px;height:345px;background:linear-gradient(var(--sky-top),var(--sky-bottom))}
.hero-text{position:absolute;left:107px;top:85px;width:620px;font-size:22px;line-height:31px;color:var(--hero-text)}
.cta{position:absolute;left:107px;top:282px;width:358px;height:42px;border-radius:21px;background:linear-gradient(#e8f1f8,#b6cadb);border:1px solid #9fb6c8;text-align:center;line-height:40px;font-size:20px;font-style:italic;color:#6d8597}
.hero-photo{position:absolute;left:800px;top:80px;width:300px;height:515px;z-index:2;transform:rotate(2deg);background:linear-gradient(135deg,#e9eef2,#b6c2cb 60%,#8e9ea9);border:6px solid #fff;box-shadow:0 4px 14px rgba(0,0,0,.3)}
.dots{position:absolute;left:930px;top:606px;display:flex;gap:7px;z-index:2}
.dots span{width:11px;height:11px;border-radius:50%;background:#e6edf2}
.dots span:first-child{background:#33434f}
.sidebar{position:absolute;left:87px;top:440px;width:203px;height:580px;background:linear-gradient(var(--side),var(--side-dark))}
.sidebar h2{font-size:30px;font-weight:700;color:#fff;margin:22px 0 0 18px}
.links{list-style:none;margin-top:12px}
.links li{height:42px;line-height:42px;padding-left:18px;font-size:17px;color:#fff}
.links li.active{background:linear-gradient(90deg,#f2f5f7,#b8c6d0);color:var(--ink)}
.follow{margin:20px 0 0 18px;font-size:30px;font-weight:700;color:#fff}
.social{display:flex;gap:22px;margin:12px 0 0 22px}
.social div{text-align:center;font-size:12px;color:#fff}
.social i{display:block;width:52px;height:52px;border-radius:10px;background:#7f98ab;margin:0 auto 4px}
.main{position:absolute;left:290px;top:440px;width:810px;height:580px;background:linear-gradient(var(--panel-light),var(--panel))}
.main h1{position:absolute;left:20px;top:18px;font-size:21px;color:#fff}
.intro{position:absolute;left:20px;top:54px;width:460px;font-size:12px;line-height:15px;color:var(--text-light)}
.quote{position:absolute;left:20px;top:172px;width:460px;height:95px}
.quote .mark{position:absolute;left:0;top:-12px;font-size:72px;font-weight:700;color:#1e2a32}
.quote p{margin-left:62px;font-size:12px;line-height:15px;font-style:italic;color:var(--text-light)}
.more{position:absolute;left:20px;top:282px;width:460px;font-size:12px;line-height:15px;color:var(--text-light)}
.readmore{position:absolute;left:390px;top:334px;padding:4px 12px;background:#3f525f;color:#fff;font-size:12px;border-radius:3px}
.recent{position:absolute;left:551px;top:200px;width:248px;height:242px;background:var(--news-box);border-radius:6px}
.recent h3{height:38px;line-height:38px;padding-left:14px;font-size:16px;font-weight:400;color:#fff;background:#5b7282;border-radius:6px 6px 0 0}
.recent ul{list-style:none;padding:8px 14px}
.recent li{font-size:12px;color:#fff;padding:7px 0 7px 12px;border-bottom:1px solid #87a0b0;position:relative}
.recent li::before{content:"";position:absolute;left:0;top:12px;width:5px;height:5px;background:#fff}
.barrier{position:absolute;left:12px;top:452px;width:105px;height:118px;background:linear-gradient(#f0c030,#d08a10);border-radius:6px}
.contact{position:absolute;left:140px;top:458px;font-size:27px;font-weight:700;color:#fff;line-height:48px;white-space:nowrap}
.footer{position:absolute;left:0;top:1020px;width:1200px;height:50px;background:var(--footer)}
.footnav{position:absolute;left:475px;top:7px;display:flex;gap:22px;font-size:12px;color:#b9c6cf}
.footnav span:first-child{color:#fff;font-weight:700}
.copy{position:absolute;right:105px;top:28px;font-size:12px;color:#fff;font-weight:700}
</style>
</head>
<body>
<header class="header">
  <div class="brand"><span class="brand-mark"></span><span class="brand-name">PELORA Keystone</span></div>
  <div class="newsfeed"><b>NEWS FEEDS</b> Lorem ipsum dolor sit amet, consectetur adipiscing elit.</div>
  <div class="datebox">
    <div><b>Todays Date:</b> 11th October 2010</div>
    <div class="times">Guam | 22:00 &nbsp; Hawaii | 22:00 &nbsp; East Coast | 22:00</div>
  </div>
</header>

<section class="hero">
  <p class="hero-text">it. In mollis rutrum metus, in blandit lacus tincidunt quis. Nam dignissim urna id nibh placerat et consectetur ligula tincidunt. Curabitur auctor arcu arcu, eget posuere sem. Praesent sed risus orci, condimentum convallis tortor. Duis egestas leo sit</p>
  <div class="cta">Click Here</div>
</section>
<div class="hero-photo" role="img" aria-label="Photo of a worker spreading tile adhesive with a trowel"></div>
<div class="dots"><span></span><span></span><span></span></div>

<nav class="sidebar">
  <h2>Quick links</h2>
  <ul class="links">
    <li class="active">Home</li>
    <li>About us</li>
    <li>Capabilities</li>
    <li>Portfolio</li>
    <li>Request for sub Bids</li>
    <li>Safety</li>
    <li>News &amp; Information</li>
  </ul>
  <div class="follow">FollowUs</div>
  <div class="social">
    <div><i></i>Friendbook</div>
    <div><i></i>Chirper</div>
  </div>
</nav>

<main class="main">
  <h1>Welcome to PELORA Keystone</h1>
  <p class="intro">Quality materials reach every site on time. Our team supplies concrete, cement, aggregates, asphalt and tile to prime and subcontractors across the island. We support federal projects with certified small business service, dependable delivery and clear technical data for each product we carry.</p>
  <div class="quote"><span class="mark">&ldquo;</span><p>Every pour starts with the right mix. We test each batch, track each load and stand behind each delivery so your crews can build with confidence from the first footing to the final finish.</p></div>
  <p class="more">Our yard stocks bulk and bagged materials year round. Request a quote for sub bids, review our safety record or read the latest news to see how we keep island projects moving.</p>
  <span class="readmore">Read More &raquo;</span>
  <aside class="recent">
    <h3>Recent News</h3>
    <ul>
      <li>New aggregate stock now available</li>
      <li>Tile product data sheets updated</li>
      <li>Yard hours extended for October</li>
      <li>Small business certification renewed</li>
      <li>Asphalt plant upgrade complete</li>
    </ul>
  </aside>
  <div class="barrier" role="img" aria-label="Illustration of a construction road barrier"></div>
  <div class="contact">Call us at 0800 5550 123<br>Email us at info@pelorakeystone.example</div>
</main>

<footer class="footer">
  <div class="footnav"><span>Home</span><span>About us</span><span>Capabilities</span><span>Portfolio</span><span>Request for sub bids</span><span>safety</span><span>News &amp; information</span></div>
  <div class="copy">Copyright 2010 PELORA Keystone</div>
</footer>
</body>
</html>
```